Plakate für Haushaltshilfen und Alltagsbegleiter
Zielgruppe
Wir bieten haushaltsnahe Dienstleistungen (Haushaltshilfen und Altgasbegleiter) für Personen mit einem Pflegegrad 1 - 5 an.
Zielgruppe sind Personen mit einem Pflegegrad 1 - 5. Hauptsächlich ältere Menschen die Unterstützung/Betreuung im Alltag und Haushalt benötigen.
Aufgabenstellung
Wir benötigen für unsere Büroräume eine Fensterbeschriftung. Es handelt sich hier um 5 Fenster (Glasflächen) und eine Glastür. Die Vorgabe ist, dass von außen zu erkennen ist dass sich um alle Räumlichkeiten um unsere (Firma Lindwerk) Räumlichkeiten handelt. Desweiteren soll auch unser Angebot erkennbar sein.
Unser Angebot enthält: Haushaltshilfen und Alltagsbegleiter
- kostenlose Haushaltshilfe ab Pflegegrad 1
- Abrechnung mit allen Kostenträgern
Da wir keine Schilder an die Fassade anbringen können, müßen die Glasflächen dafür genutzt werden um zum Einen uns als Firma erkennbar zu machen und zum anderen unser Angebot kurz zu präsentieren.
Uns ist wichtig dass unser Logo verwendet wir und auch unsere Farben.
Desweiteren sollten an den Fenstern auch teilweise eine Sichtschutz nach innen, angebracht werden, aber eben nur teilweise also nicht das ganzen Fenster z.Bsp. mit einer Blickdichten Folie überziehen, sondern in Augenhöhe wenn Fußgänger vorbei laufen.

```html
<!DOCTYPE html>
<html lang="de">
<head>
<meta charset="utf-8">
<title>Lindwerk – Plakate und Fensterbeschriftung</title>
<link href="https://fonts.googleapis.com/css2?family=Cinzel:wght@700&family=Montserrat:wght@300;600;700&family=Gochi+Hand&display=swap" rel="stylesheet">
<style>
:root{
  --red:#c8161d;
  --red-text:#c4161c;
  --paper:#f2f2f0;
  --ink:#333333;
  --dark:#3a3a3a;
  --stage:#bfbfc0;
  --white:#ffffff;
}
*{margin:0;padding:0;box-sizing:border-box}
html,body{width:723px;height:1200px;overflow:hidden}
body{background:var(--stage);position:relative;font-family:'Montserrat',sans-serif}

.poster{position:absolute;top:74px;width:207px;height:288px;background:var(--paper);overflow:hidden;box-shadow:0 2px 4px rgba(0,0,0,.25)}
.poster--household{left:33px}
.poster--shopping{left:258px}
.poster--companion{left:483px}
.poster__title{position:absolute;top:16px;left:0;width:100%;text-align:center;font-family:'Cinzel',serif;font-weight:700;color:var(--red-text);line-height:1}
.poster--household .poster__title{font-size:18px}
.poster--shopping .poster__title{font-size:17px}
.poster--companion .poster__title{font-size:15px;top:18px}
.poster__band{position:absolute;top:54px;left:0;width:100%;height:126px;background:var(--red);overflow:hidden}
.poster__heading{position:absolute;top:18px;left:10px;width:110px;color:var(--white);font-weight:600;font-size:9.5px;line-height:1.15}
.poster__bullets{position:absolute;top:48px;left:10px;width:75px;list-style:none;color:var(--white);font-weight:300;font-size:7.2px;line-height:1.15}
.poster__bullets li{position:relative;padding-left:6px;margin-bottom:6px}
.poster__bullets li::before{content:"·";position:absolute;left:0}
.poster__photo{position:absolute;top:13px;left:98px;width:210px;height:210px;border-radius:50%;border:2px solid var(--paper)}
.poster--household .poster__photo{background:radial-gradient(circle at 40% 40%,#b9a89a,#6d5d52 70%)}
.poster--shopping .poster__photo{background:radial-gradient(circle at 45% 45%,#c9b79a,#6f5a44 70%)}
.poster--companion .poster__photo{background:radial-gradient(circle at 40% 40%,#b8aaa2,#5f5856 70%)}
.poster__icon{position:absolute;top:78px;left:82px;width:38px;height:38px;border-radius:50%;background:var(--paper);display:flex;align-items:center;justify-content:center}
.poster__tagline{position:absolute;top:192px;left:0;width:100%;text-align:center;font-family:'Gochi Hand',cursive;color:var(--red-text);font-size:14px}
.brand{position:absolute;left:0;width:100%;text-align:center}
.brand__mark{display:block;margin:0 auto;border:2px solid var(--red);border-radius:50%}
.brand__name{display:block;font-family:'Cinzel',serif;font-weight:700;color:var(--ink);line-height:1}
.brand__sub{display:block;font-family:'Cinzel',serif;font-weight:700;color:var(--red-text);line-height:1.2}
.poster .brand{top:212px}
.poster .brand__mark{width:24px;height:24px;margin-bottom:4px}
.poster .brand__name{font-size:11px}
.poster .brand__sub{font-size:4px}
.poster__contact{position:absolute;bottom:0;left:0;width:100%;height:21px;background:var(--dark);display:flex;justify-content:space-between;align-items:center;padding:0 10px;color:var(--white);font-size:5px}
.contact-item{display:flex;align-items:center;gap:3px;white-space:nowrap}
.contact-item svg{flex:none}

.window-sign{position:absolute;top:440px;width:175px;height:290px;background:var(--white);overflow:hidden;box-shadow:0 2px 4px rgba(0,0,0,.25)}
.window-sign--left{left:51px}
.window-sign--right{left:497px}
.window-sign__screen{position:absolute;top:0;left:0;width:100%;height:82px;background:linear-gradient(#1e1e1e 20%,#7a7a7a 60%,#ffffff)}
.window-sign .brand{top:92px}
.window-sign .brand__mark{width:28px;height:28px;margin-bottom:5px}
.window-sign .brand__name{font-size:14px}
.window-sign .brand__sub{font-size:5px}
.window-sign__heading{position:absolute;top:152px;left:0;width:100%;text-align:center;font-weight:600;font-size:7px;color:var(--ink)}
.window-sign__points{position:absolute;top:166px;left:0;width:100%;text-align:center;font-weight:300;font-size:5.5px;line-height:1.7;color:var(--ink);list-style:none}
.window-sign__footer{position:absolute;bottom:0;left:0;width:100%;height:68px;background:var(--dark);color:var(--white);text-align:center}
.window-sign__cta{margin-top:12px;font-weight:700;font-size:8px}
.window-sign__contact{display:flex;justify-content:space-between;padding:0 12px;margin-top:9px;font-size:4.6px}
.window-sign__web{margin-top:9px;font-weight:700;font-size:5.5px}

.door-sign{position:absolute;top:420px;left:286px;width:150px;height:380px;background:var(--white);overflow:hidden;box-shadow:0 2px 4px rgba(0,0,0,.25)}
.door-sign__screen{position:absolute;left:0;width:100%;height:120px}
.door-sign__screen--top{top:0;background:linear-gradient(#1e1e1e 20%,#7a7a7a 60%,#ffffff)}
.door-sign__screen--bottom{bottom:0;background:linear-gradient(#ffffff,#7a7a7a 40%,#1e1e1e 80%)}
.door-sign .brand{top:150px}
.door-sign .brand__mark{width:34px;height:34px;margin-bottom:6px}
.door-sign .brand__name{font-size:16px}
.door-sign .brand__sub{font-size:5.5px}
</style>
</head>
<body>

<article class="poster poster--household">
  <h2 class="poster__title">HAUSHALTSHILFE</h2>
  <div class="poster__band">
    <p class="poster__heading">Haushaltshilfen und Alltagsbegleiter</p>
    <ul class="poster__bullets">
      <li>kostenlose Haushaltshilfe ab Pflegegrad 1</li>
      <li>Abrechnung mit allen Kostenträgern</li>
    </ul>
    <div class="poster__photo" role="img" aria-label="Foto: Helferin und ältere Dame am Tisch"></div>
    <div class="poster__icon" role="img" aria-label="Symbol Haushalt"></div>
  </div>
  <p class="poster__tagline">Wir sind für Sie da!</p>
  <div class="brand"><span class="brand__mark"></span><span class="brand__name">LINDWERK</span><span class="brand__sub">HAUSHALTSHILFEN &amp; MEHR</span></div>
  <footer class="poster__contact">
    <span class="contact-item"><svg width="6" height="6" viewBox="0 0 24 24"><path fill="#fff" d="M6.6 10.8a15 15 0 0 0 6.6 6.6l2.2-2.2a1 1 0 0 1 1-.25 11.4 11.4 0 0 0 3.6.6 1 1 0 0 1 1 1V20a1 1 0 0 1-1 1A17 17 0 0 1 3 4a1 1 0 0 1 1-1h3.5a1 1 0 0 1 1 1c0 1.25.2 2.45.6 3.6a1 1 0 0 1-.25 1z"/></svg>0711 20 30 40 50</span>
    <span class="contact-item"><svg width="6" height="6" viewBox="0 0 10 10"><circle cx="5" cy="5" r="4" fill="none" stroke="#fff" stroke-width="1"/></svg>0176 10 20 30 40</span>
    <span class="contact-item"><svg width="7" height="5" viewBox="0 0 14 10"><rect x=".5" y=".5" width="13" height="9" fill="none" stroke="#fff"/><path d="M.5 .5 7 6 13.5 .5" fill="none" stroke="#fff"/></svg>info@lindwerk.de</span>
  </footer>
</article>

<article class="poster poster--shopping">
  <h2 class="poster__title">EINKAUFSSERVICE</h2>
  <div class="poster__band">
    <p class="poster__heading">Haushaltshilfen und Alltagsbegleiter</p>
    <ul class="poster__bullets">
      <li>kostenlose Haushaltshilfe ab Pflegegrad 1</li>
      <li>Abrechnung mit allen Kostenträgern</li>
    </ul>
    <div class="poster__photo" role="img" aria-label="Foto: junge Begleiterin und ältere Dame beim Einkauf"></div>
    <div class="poster__icon" role="img" aria-label="Symbol Einkaufstüte"></div>
  </div>
  <p class="poster__tagline">Wir sind für Sie da!</p>
  <div class="brand"><span class="brand__mark"></span><span class="brand__name">LINDWERK</span><span class="brand__sub">HAUSHALTSHILFEN &amp; MEHR</span></div>
  <footer class="poster__contact">
    <span class="contact-item"><svg width="6" height="6" viewBox="0 0 24 24"><path fill="#fff" d="M6.6 10.8a15 15 0 0 0 6.6 6.6l2.2-2.2a1 1 0 0 1 1-.25 11.4 11.4 0 0 0 3.6.6 1 1 0 0 1 1 1V20a1 1 0 0 1-1 1A17 17 0 0 1 3 4a1 1 0 0 1 1-1h3.5a1 1 0 0 1 1 1c0 1.25.2 2.45.6 3.6a1 1 0 0 1-.25 1z"/></svg>0711 20 30 40 50</span>
    <span class="contact-item"><svg width="6" height="6" viewBox="0 0 10 10"><circle cx="5" cy="5" r="4" fill="none" stroke="#fff" stroke-width="1"/></svg>0176 10 20 30 40</span>
    <span class="contact-item"><svg width="7" height="5" viewBox="0 0 14 10"><rect x=".5" y=".5" width="13" height="9" fill="none" stroke="#fff"/><path d="M.5 .5 7 6 13.5 .5" fill="none" stroke="#fff"/></svg>info@lindwerk.de</span>
  </footer>
</article>

<article class="poster poster--companion">
  <h2 class="poster__title">ALLTAGSBEGLEITUNG</h2>
  <div class="poster__band">
    <p class="poster__heading">Haushaltshilfen und Alltagsbegleiter</p>
    <ul class="poster__bullets">
      <li>kostenlose Haushaltshilfe ab Pflegegrad 1</li>
      <li>Abrechnung mit allen Kostenträgern</li>
    </ul>
    <div class="poster__photo" role="img" aria-label="Foto: helfende Hände auf einem Gehstock"></div>
    <div class="poster__icon" role="img" aria-label="Symbol Fürsorge"></div>
  </div>
  <p class="poster__tagline">Wir sind für Sie da!</p>
  <div class="brand"><span class="brand__mark"></span><span class="brand__name">LINDWERK</span><span class="brand__sub">HAUSHALTSHILFEN &amp; MEHR</span></div>
  <footer class="poster__contact">
    <span class="contact-item"><svg width="6" height="6" viewBox="0 0 24 24"><path fill="#fff" d="M6.6 10.8a15 15 0 0 0 6.6 6.6l2.2-2.2a1 1 0 0 1 1-.25 11.4 11.4 0 0 0 3.6.6 1 1 0 0 1 1 1V20a1 1 0 0 1-1 1A17 17 0 0 1 3 4a1 1 0 0 1 1-1h3.5a1 1 0 0 1 1 1c0 1.25.2 2.45.6 3.6a1 1 0 0 1-.25 1z"/></svg>0711 20 30 40 50</span>
    <span class="contact-item"><svg width="6" height="6" viewBox="0 0 10 10"><circle cx="5" cy="5" r="4" fill="none" stroke="#fff" stroke-width="1"/></svg>0176 10 20 30 40</span>
    <span class="contact-item"><svg width="7" height="5" viewBox="0 0 14 10"><rect x=".5" y=".5" width="13" height="9" fill="none" stroke="#fff"/><path d="M.5 .5 7 6 13.5 .5" fill="none" stroke="#fff"/></svg>info@lindwerk.de</span>
  </footer>
</article>

<section class="window-sign window-sign--left">
  <div class="window-sign__screen" role="img" aria-label="Sichtschutz-Raster, dunkel nach hell verlaufend"></div>
  <div class="brand"><span class="brand__mark"></span><span class="brand__name">LINDWERK</span><span class="brand__sub">HAUSHALTSHILFEN &amp; MEHR</span></div>
  <p class="window-sign__heading">Haushaltshilfen und Alltagsbegleiter</p>
  <ul class="window-sign__points">
    <li>kostenlose Haushaltshilfe ab Pflegegrad 1</li>
    <li>Abrechnung mit allen Kostenträgern</li>
  </ul>
  <footer class="window-sign__footer">
    <p class="window-sign__cta">Jetzt Termin vereinbaren!</p>
    <div class="window-sign__contact"><span>0711 20 30 40 50</span><span>0176 10 20 30 40</span><span>info@lindwerk.de</span></div>
    <p class="window-sign__web">www.lindwerk.de</p>
  </footer>
</section>

<section class="door-sign">
  <div class="door-sign__screen door-sign__screen--top" role="img" aria-label="Sichtschutz-Raster, dunkel nach hell verlaufend"></div>
  <div class="brand"><span class="brand__mark"></span><span class="brand__name">LINDWERK</span><span class="brand__sub">HAUSHALTSHILFEN &amp; MEHR</span></div>
  <div class="door-sign__screen door-sign__screen--bottom" role="img" aria-label="Sichtschutz-Raster, hell nach dunkel verlaufend"></div>
</section>

<section class="window-sign window-sign--right">
  <div class="window-sign__screen" role="img" aria-label="Sichtschutz-Raster, dunkel nach hell verlaufend"></div>
  <div class="brand"><span class="brand__mark"></span><span class="brand__name">LINDWERK</span><span class="brand__sub">HAUSHALTSHILFEN &amp; MEHR</span></div>
  <p class="window-sign__heading">Haushaltshilfen und Alltagsbegleiter</p>
  <ul class="window-sign__points">
    <li>kostenlose Haushaltshilfe ab Pflegegrad 1</li>
    <li>Abrechnung mit allen Kostenträgern</li>
  </ul>
  <footer class="window-sign__footer">
    <p class="window-sign__cta">Jetzt Termin vereinbaren!</p>
    <div class="window-sign__contact"><span>0711 20 30 40 50</span><span>0176 10 20 30 40</span><span>info@lindwerk.de</span></div>
    <p class="window-sign__web">www.lindwerk.de</p>
  </footer>
</section>

</body>
</html>
```